OrchardLane Kiosk Signage

OrchardLane sell fresh fruit and vegetables online and from road side Kiosks.

We need to adapt the current logo for use as signs that will be displayed on roadside kiosks, please see the attached images to view and understand what the Kiosks look like.
The sign needs to:

1. Capture the attention of drivers and
2. Invite them to stop and purchase fresh fruit and veg
3. Communicate the URL www.OrchardLaneProduce.example.nz
4. Communicate the OrchardLane brand
5. Use current logos and imagery

Solution

The designs must closely reflect the current OrchardLane logo (see files attached) and need to include the website. www.OrchardLaneProduce.example.nz The colour palleted also needs to closely resemble the website.

The designs will be used for laser printed signage on vinyl for two applications

1. Kiosk front width: 2.400m x height: 1.000m (94 inches x 40 inches)
2. Kiosk sides: width 0.400m x height: 1.000m (15 inches x 40 inches)

The region where the kiosk's will display is large open space, green hills and fresh fruit and veg growers (orchards and farms everywhere). The region is well known for horticulture, agriculture, viticulture and farming.

The Kiosk images are attached (P1340537, P1350158, P1350159)
OrchardLane logo (round tree)
OrchardLane logo
Updates

Please note, the OrchardLane kiosk signage brief has been updated. (sorry for the inconvenience, but I think we uploaded an unfinished brief) 

We look forward to your submissions. 

Cheers, OrchardLane 

Target Market(s)

Passers buy - mainly in cars as the signage will be displayed on road side fruit and veg stalls. So the signage will be viewed by the general public, and capture those that are interested in purchasing fresh fruit and veg (direct from the farm or orchard)

Industry/Entity Type

Agriculture

Requirements
Must have
• Must match current logo and reflect the design aspects of the website www.orchardlaneproduce.example.nz
Needs to clearly communicate whats for sale, value and fresh produce
Nice to have
• It would be nice to make the tree component of the logo a feature.

```html
<!DOCTYPE html>
<html lang="en">
<head>
<meta charset="utf-8">
<title>OrchardLane Kiosk Sign</title>
<link rel="stylesheet" href="https://fonts.googleapis.com/css2?family=Rubik+Dirt&family=Arimo:wght@400&display=swap">
<style>
  :root {
    --brand-green: #6f8c5e;
    --band-green: rgba(104, 136, 88, 0.82);
    --white: #ffffff;
    --onion: #c9743f;
    --onion-light: #e09a62;
    --pea: #7fb43a;
    --pea-light: #a6cf5c;
    --tomato: #d8261c;
    --tomato-light: #ee4a34;
    --eggplant: #2a2030;
    --eggplant-light: #5a4a66;
    --sky: #3c6fc4;
    --potato: #d9a551;
    --potato-light: #ecc47a;
    --caption: #222222;
  }
  html, body {
    margin: 0;
    padding: 0;
    width: 1200px;
    height: 748px;
    overflow: hidden;
    background: var(--white);
  }
  .sign {
    position: relative;
    width: 1200px;
    height: 748px;
    background: var(--white);
    font-family: "Rubik Dirt", "Arial Black", sans-serif;
  }
  .produce-strip {
    position: absolute;
    left: 0;
    top: 0;
    width: 1200px;
    height: 718px;
    display: flex;
  }
  .produce { height: 100%; }
  .produce--onions   { width: 240px; background: radial-gradient(circle at 40% 45%, var(--onion-light), var(--onion)); }
  .produce--peas     { width: 207px; background: radial-gradient(circle at 50% 50%, var(--pea-light), var(--pea)); }
  .produce--tomatoes { width: 260px; background: radial-gradient(circle at 50% 40%, var(--tomato-light), var(--tomato)); }
  .produce--eggplant { width: 248px; background: linear-gradient(100deg, var(--eggplant) 0%, var(--eggplant-light) 45%, var(--eggplant) 70%, var(--sky) 100%); }
  .produce--potatoes { width: 245px; background: radial-gradient(circle at 50% 45%, var(--potato-light), var(--potato)); }

  .inner-frame {
    position: absolute;
    left: 33px;
    top: 30px;
    width: 1133px;
    height: 665px;
    border: 2px solid var(--white);
  }
  .message-band {
    position: absolute;
    left: 0;
    top: 262px;
    width: 1200px;
    height: 188px;
    background: var(--band-green);
    text-align: center;
    color: var(--white);
  }
  .headline {
    margin: 0;
    padding-top: 24px;
    font-size: 70px;
    font-weight: 400;
    letter-spacing: 1px;
    line-height: 1;
    white-space: nowrap;
  }
  .tagline {
    margin: 22px 0 0;
    font-size: 35px;
    font-weight: 400;
    letter-spacing: 0.5px;
    line-height: 1;
    white-space: nowrap;
  }
  .emblem {
    position: absolute;
    left: 47px;
    top: 545px;
    width: 132px;
    height: 132px;
  }
  .web-address {
    position: absolute;
    left: 178px;
    top: 627px;
    width: 523px;
    height: 48px;
    box-sizing: content-box;
    background: var(--brand-green);
    border: 2px solid var(--white);
    color: var(--white);
    font-family: "Arimo", Arial, sans-serif;
    font-size: 29px;
    line-height: 48px;
    text-align: center;
    white-space: nowrap;
    overflow: hidden;
  }
  .brand-block {
    position: absolute;
    left: 848px;
    top: 527px;
    width: 300px;
    height: 152px;
    background: var(--white);
    border-radius: 14px;
    box-sizing: border-box;
    padding: 10px;
  }
  .brand-block__panel {
    width: 100%;
    height: 100%;
    background: var(--brand-green);
    border-radius: 10px;
    display: flex;
    align-items: center;
    justify-content: center;
    overflow: hidden;
  }
  .brand-block__name {
    color: var(--white);
    font-size: 32px;
    letter-spacing: 0.5px;
    white-space: nowrap;
  }
  .spec-caption {
    position: absolute;
    right: 12px;
    top: 727px;
    margin: 0;
    font-family: "Arimo", Arial, sans-serif;
    font-size: 14px;
    color: var(--caption);
    white-space: pre;
  }
</style>
</head>
<body>
  <main class="sign">
    <div class="produce-strip">
      <div class="produce produce--onions" role="img" aria-label="Photo of brown onions"></div>
      <div class="produce produce--peas" role="img" aria-label="Photo of fresh green peas"></div>
      <div class="produce produce--tomatoes" role="img" aria-label="Photo of ripe red tomatoes"></div>
      <div class="produce produce--eggplant" role="img" aria-label="Photo of purple eggplants against a blue sky"></div>
      <div class="produce produce--potatoes" role="img" aria-label="Photo of golden potatoes"></div>
    </div>

    <div class="inner-frame"></div>

    <section class="message-band">
      <h1 class="headline">From the Farm to Your Table</h1>
      <p class="tagline">OrchardLane is a family owned and operated business.</p>
    </section>

    <svg class="emblem" viewBox="0 0 132 132" aria-hidden="true">
      <circle cx="66" cy="66" r="62" fill="var(--brand-green)" stroke="var(--white)" stroke-width="4"/>
    </svg>

    <div class="web-address">www.orchardlaneproduce.example.nz</div>

    <div class="brand-block">
      <div class="brand-block__panel">
        <span class="brand-block__name">OrchardLane</span>
      </div>
    </div>

    <p class="spec-caption">General Purpose  sign  1000mm x 600mm</p>
  </main>
</body>
</html>
```